New Business Card Design

We would like to refresh our business cards and make them look better. We are an IT company specialising in Cloud Services, IT Managed Services, software and hardware. I have attached a PSD of our current design. Also attached our logo.
Updates

I have uploaded all new logos in EPS format.

Can you please edit all designs to include a job title for Marcus Hollis, eg. General Manager

Industry/Entity Type

Software

Colors
ffffff

Requirements
Must have
• Please use white background.
Should not have
• Black background

```html
<!DOCTYPE html>
<html lang="en">
<head>
<meta charset="utf-8">
<title>clearpath systems – Business Card</title>
<link href="https://fonts.googleapis.com/css2?family=Open+Sans:wght@300;400;600&display=swap" rel="stylesheet">
<style>
  :root {
    --stage: #e9e6e2;
    --card-white: #ffffff;
    --brand-red: #c0392b;
    --band-grey: #8a9199;
    --text-dark: #3b3b3b;
    --text-mid: #555a60;
    --text-white: #ffffff;
    --divider: #c9cdd1;
  }
  * { box-sizing: border-box; margin: 0; padding: 0; }
  html, body { width: 1200px; height: 720px; overflow: hidden; }
  body {
    background: var(--stage);
    font-family: "Open Sans", Arial, sans-serif;
    position: relative;
  }
  .card {
    position: absolute;
    top: 205px;
    width: 540px;
    height: 310px;
    box-shadow: 0 6px 18px rgba(0,0,0,0.15);
    overflow: hidden;
  }
  /* ---------- front ---------- */
  .card-front { left: 45px; background: var(--card-white); }
  .brand {
    position: absolute;
    top: 52px;
    left: 0; right: 0;
    display: flex;
    justify-content: center;
    align-items: center;
    gap: 14px;
  }
  .brand-dot {
    width: 34px; height: 34px;
    border-radius: 50%;
    background: var(--brand-red);
  }
  .brand-name {
    font-weight: 300;
    font-size: 38px;
    letter-spacing: 5px;
    color: var(--text-dark);
    line-height: 1;
  }
  .name-band {
    position: absolute;
    top: 142px; left: 0; right: 0;
    height: 30px;
    background: var(--band-grey);
    border-top: 2px solid var(--brand-red);
    outline: 3px solid var(--card-white);
    display: flex;
    align-items: center;
    justify-content: center;
    color: var(--text-white);
  }
  .name-band::before {
    content: "";
    position: absolute;
    left: 0; right: 0; top: -8px;
    border-top: 1px solid var(--brand-red);
  }
  .person-name { font-weight: 600; font-size: 16px; }
  .person-title { font-weight: 400; font-size: 12px; margin-left: 6px; }
  .footer-band {
    position: absolute;
    top: 270px; left: 0; right: 0;
    height: 14px;
    background: var(--band-grey);
    border-top: 2px solid var(--brand-red);
  }
  .contacts {
    position: absolute;
    top: 190px; left: 0; right: 0;
    display: flex;
    justify-content: center;
    gap: 22px;
  }
  .contact-col {
    display: flex;
    flex-direction: column;
    gap: 8px;
  }
  .contact-col + .contact-col {
    border-left: 1px solid var(--divider);
    padding-left: 22px;
  }
  .contact-line {
    display: flex;
    align-items: center;
    gap: 7px;
    font-size: 12.5px;
    color: var(--text-mid);
  }
  .contact-line svg { width: 12px; height: 12px; flex: none; }
  /* ---------- back ---------- */
  .card-back { left: 615px; background: var(--brand-red); color: var(--text-white); text-align: center; }
  .back-brand {
    position: absolute;
    top: 44px; left: 0; right: 0;
    display: flex;
    flex-direction: column;
    align-items: center;
    gap: 12px;
  }
  .back-dot {
    width: 84px; height: 84px;
    border-radius: 50%;
    background: var(--card-white);
  }
  .back-brand-name {
    font-weight: 300;
    font-size: 26px;
    letter-spacing: 4px;
    color: var(--text-white);
  }
  .tagline {
    position: absolute;
    top: 200px; left: 0; right: 0;
    font-size: 15px;
    line-height: 1.45;
  }
  .back-url {
    position: absolute;
    top: 258px; left: 0; right: 0;
    font-size: 11px;
    letter-spacing: 3px;
  }
</style>
</head>
<body>

<section class="card card-front" aria-label="Business card front">
  <div class="brand">
    <span class="brand-dot"></span>
    <span class="brand-name">clearpath systems</span>
  </div>

  <div class="name-band">
    <span class="person-name">Marcus Hollis,</span>
    <span class="person-title">General Manager</span>
  </div>

  <div class="contacts">
    <div class="contact-col">
      <div class="contact-line">
        <svg viewBox="0 0 12 12"><circle cx="6" cy="6" r="5.5" fill="none" stroke="#c0392b"/><path d="M4 3.5 L5 3.5 L5.5 5 L4.8 5.5 Q5.5 7 6.5 7.2 L7 6.5 L8.5 7 L8.5 8 Q6 8.5 4.5 6.5 Q3.5 5 4 3.5Z" fill="#c0392b"/></svg>
        <span>07 5550 1234</span>
      </div>
      <div class="contact-line">
        <svg viewBox="0 0 12 12"><rect x="3" y="1" width="6" height="10" rx="1" fill="#c0392b"/><rect x="4" y="2.5" width="4" height="4" fill="#fff"/></svg>
        <span>0400 555 017</span>
      </div>
    </div>
    <div class="contact-col">
      <div class="contact-line">
        <svg viewBox="0 0 12 12"><rect x="1" y="2.5" width="10" height="7" fill="#c0392b"/><path d="M1 2.5 L6 6.5 L11 2.5" fill="none" stroke="#fff" stroke-width="1"/></svg>
        <span>mhollis@clearpathit.com.au</span>
      </div>
      <div class="contact-line">
        <svg viewBox="0 0 12 12"><circle cx="6" cy="6" r="5.5" fill="#c0392b"/><path d="M1 6 H11 M6 0.5 V11.5 M2 3.5 H10 M2 8.5 H10" stroke="#fff" stroke-width="0.7" fill="none"/></svg>
        <span>www.clearpathit.com.au</span>
      </div>
    </div>
  </div>

  <div class="footer-band"></div>
</section>

<section class="card card-back" aria-label="Business card back">
  <div class="back-brand">
    <span class="back-dot"></span>
    <span class="back-brand-name">clearpath systems</span>
  </div>
  <p class="tagline">We are an IT company specializing in Cloud Services<br>IT Managed Services, software and hardware</p>
  <p class="back-url">www.clearpathit.com.au</p>
</section>

</body>
</html>
```